Varnex Consulting Business card design.

See our website www.varnexconsulting.example which will give you a good idea of what we are about. The font is called 'Play'.

I'd like a standout business card in keeping with the themes and branding on the website

Target Market(s)

professionals. HR directors

Industry/Entity Type

Business

Contact Information for Business Card

Varnex Consulting PO Box 3172 Merrowdale NSW 2291 1300 485 193 Gavin Threlkeld Principal email: career@varnexconsulting.example ABN: 71203948865

Font styles to use
Other font styles liked:
• Play

Requirements
Must have
• Must have same design colours and branding as website.
• On back I'd prefer a list of the things we do which appears below the name at the header on the website

```html
<!DOCTYPE html>
<html lang="en">
<head>
<meta charset="utf-8">
<title>Varnex Consulting – Business Card</title>
<link rel="stylesheet" href="https://fonts.googleapis.com/css2?family=Play:wght@400;700&display=swap">
<style>
  :root {
    --page-bg: #e9ebee;
    --navy-deep: #0b2138;
    --navy: #123757;
    --navy-light: #1c4c73;
    --cyan: #2fb2e6;
    --white: #ffffff;
    --photo-top: #e4e6ea;
    --photo-mid: #c9ced4;
    --photo-sea: #6fa7ad;
    --rule: rgba(255,255,255,0.75);
  }
  * { box-sizing: border-box; margin: 0; padding: 0; }
  html, body {
    width: 1200px; height: 902px; overflow: hidden;
    background: var(--page-bg);
    font-family: 'Play', sans-serif;
  }
  .card {
    position: absolute;
    left: 250px;
    width: 700px; height: 400px;
    overflow: hidden;
    border-radius: 4px;
    box-shadow: 0 6px 18px rgba(0,0,0,0.18);
  }
  .card--front { top: 40px; }
  .card--back {
    top: 462px;
    background: radial-gradient(ellipse at 45% 35%, var(--navy-light) 0%, var(--navy) 45%, var(--navy-deep) 100%);
  }

  /* Front */
  .hero-photo {
    position: absolute; inset: 0;
    background: linear-gradient(180deg, var(--photo-top) 0%, var(--photo-mid) 50%, var(--photo-sea) 85%);
  }
  .front-band {
    position: absolute; left: 0; right: 0; bottom: 0; height: 120px;
    background: linear-gradient(180deg, rgba(18,55,87,0.92), var(--navy-deep));
  }
  .front-band .brand { position: absolute; right: 60px; top: 22px; text-align: left; }

  .brand-name {
    font-weight: 400; color: var(--white);
    letter-spacing: 1px; text-transform: uppercase; white-space: nowrap;
  }
  .front-band .brand-name { font-size: 40px; }
  .services {
    color: var(--cyan); font-size: 12.5px; letter-spacing: 0.6px;
    margin-top: 6px; white-space: nowrap;
  }

  /* Back */
  .card--back .brand { position: absolute; left: 55px; top: 50px; }
  .card--back .brand-name { font-size: 46px; }
  .card--back .services { font-size: 13.5px; }

  .rule { position: absolute; height: 1.5px; background: var(--rule); }
  .rule--main { left: 0; top: 200px; width: 420px; }
  .rule--tail { left: 668px; top: 152px; width: 32px; }

  .person { position: absolute; right: 44px; top: 135px; text-align: right; }
  .person-name { color: var(--cyan); font-size: 29px; font-weight: 700; line-height: 1; }
  .person-role { color: var(--white); font-size: 19px; margin-top: 4px; }

  .abn { position: absolute; left: 60px; top: 238px; color: var(--white); font-size: 22px; }
  .contacts { position: absolute; left: 72px; top: 282px; list-style: none; }
  .contacts li {
    display: flex; align-items: center; gap: 14px;
    color: var(--white); font-size: 17px; height: 28px;
  }
  .contact-icon { width: 18px; height: 18px; flex: none; }
</style>
</head>
<body>

<section class="card card--front">
  <div class="hero-photo" role="img" aria-label="Photograph of a surfer in a wetsuit riding a breaking wave"></div>
  <div class="front-band">
    <div class="brand">
      <div class="brand-name">Varnex Consulting</div>
      <div class="services">Search &amp; Select | Career | Coaching | Leadership | Outplacement</div>
    </div>
  </div>
</section>

<section class="card card--back">
  <div class="brand">
    <div class="brand-name">Varnex Consulting</div>
    <div class="services">Search &amp; Select | Career | Coaching | Leadership | Outplacement</div>
  </div>

  <div class="rule rule--main"></div>
  <div class="rule rule--tail"></div>

  <div class="person">
    <div class="person-name">Gavin Threlkeld</div>
    <div class="person-role">Principal</div>
  </div>

  <div class="abn">ABN: 71203948865</div>

  <ul class="contacts">
    <li>
      <svg class="contact-icon" viewBox="0 0 18 18" aria-hidden="true">
        <rect width="18" height="18" rx="2" fill="var(--cyan)"/>
        <path d="M5 4.5c.6-.4 1.3-.3 1.6.3l.9 1.6c.2.4.1.9-.3 1.2l-.6.5c.6 1.3 1.6 2.3 2.9 2.9l.5-.6c.3-.4.8-.5 1.2-.3l1.6.9c.6.3.7 1 .3 1.6l-.6.8c-.5.6-1.3.8-2 .5C7.6 12.8 5.2 10.4 4.1 7.5c-.3-.7-.1-1.5.5-2z" fill="var(--navy-deep)"/>
      </svg>
      1300 485 193
    </li>
    <li>
      <svg class="contact-icon" viewBox="0 0 18 18" aria-hidden="true">
        <rect width="18" height="18" rx="2" fill="var(--cyan)"/>
        <rect x="3.5" y="5" width="11" height="8" fill="none" stroke="var(--navy-deep)" stroke-width="1.4"/>
        <path d="M3.5 5.3 9 9.6l5.5-4.3" fill="none" stroke="var(--navy-deep)" stroke-width="1.4"/>
      </svg>
      career@varnexconsulting.example
    </li>
    <li>
      <svg class="contact-icon" viewBox="0 0 18 18" aria-hidden="true">
        <rect width="18" height="18" rx="2" fill="var(--cyan)"/>
        <path d="M9 3.5a3.8 3.8 0 0 0-3.8 3.8c0 2.8 3.8 7.2 3.8 7.2s3.8-4.4 3.8-7.2A3.8 3.8 0 0 0 9 3.5z" fill="var(--navy-deep)"/>
        <circle cx="9" cy="7.3" r="1.4" fill="var(--cyan)"/>
      </svg>
      PO Box 3172 Merrowdale NSW 2291
    </li>
  </ul>
</section>

</body>
</html>
```